Assessment Report cover design and formatting

This report is for senior executives and provides leaders with detailed insight into their capabilities and skills. The cover should have space for the date and name of the person doing the assessment. We are looking to modernise the report cover design. We would like the report to be our company colours if possible. The work will likely expand once the cover is done to other parts of the report, ie. the format and layout of the report etc.

Company colours:
Primary colours:
• Blue #0D47A1, #115CD0, #90B6ED, #EEf3FB
• Green #0D91A1, #47A10D, #324C196, #0DA11D
Additional colours:
• Purple #A10D91
• Brown #A1670D
• Red #A10D47

Target Market(s)

Executives

Industry/Entity Type

Consulting, leadership development

Colors
0094D4
00A9DD
6FCCEA
C7EBF8
E9F6FB
00AB8E
00BBA5
67D7C9
C6EFE9
E9F9F6
E54698
E96AAD
F1A4CE
F9D9EA
FCEFF6
6B429C
8869AF
B7A5CE
E3DAEB
F3F0F8

Requirements
Must have
• The report cover should have space for name of user, the date and company logo. Cover should be in A4 size.

```html
<!DOCTYPE html>
<html lang="en">
<head>
<meta charset="utf-8">
<title>Growth Leader Assessment – Report Cover</title>
<link rel="stylesheet" href="https://fonts.googleapis.com/css2?family=Poppins:wght@400;500;600&display=swap">
<style>
  :root {
    --backdrop: #adc5d1;
    --paper: #ffffff;
    --brand-blue: #1a3fa0;
    --brand-purple: #a10d91;
    --brand-green: #23c295;
    --ink: #3a3a3a;
    --ink-soft: #444444;
    --sky-top: #d3d7dc;
    --sky-mid: #b7a9a8;
    --tower-warm: #7a4531;
    --tower-dark: #2a1f1c;
  }
  * { margin: 0; padding: 0; box-sizing: border-box; }
  html, body {
    width: 943px;
    height: 1200px;
    overflow: hidden;
    background: var(--backdrop);
    font-family: "Poppins", sans-serif;
  }
  .cover {
    position: absolute;
    left: 47px;
    top: 0;
    width: 848px;
    height: 1200px;
    background: var(--paper);
    overflow: hidden;
  }
  .accent-band {
    position: absolute;
    left: 704px;
    width: 144px;
    background: var(--brand-purple);
  }
  .accent-band--top { top: 0; height: 400px; }
  .accent-band--bottom { top: 1070px; height: 130px; }
  .hero-photo {
    position: absolute;
    left: 339px;
    top: 400px;
    width: 509px;
    height: 670px;
    background:
      linear-gradient(200deg, var(--sky-top) 0%, var(--sky-mid) 35%, var(--tower-warm) 62%, var(--tower-dark) 100%);
  }
  .brand {
    position: absolute;
    left: 72px;
    top: 118px;
    color: var(--brand-blue);
    font-weight: 500;
    font-size: 30px;
    line-height: 1.2;
    white-space: nowrap;
  }
  .title {
    position: absolute;
    left: 70px;
    top: 278px;
    font-weight: 600;
    color: var(--ink);
    font-size: 72px;
    line-height: 1;
    letter-spacing: -3px;
    white-space: nowrap;
  }
  .title-tag {
    position: absolute;
    left: 72px;
    top: 350px;
    width: 486px;
    height: 102px;
    background: var(--brand-green);
    color: var(--paper);
    font-weight: 600;
    font-size: 74px;
    line-height: 106px;
    letter-spacing: -3px;
    padding-left: 24px;
    white-space: nowrap;
  }
  .recipient {
    position: absolute;
    left: 70px;
    top: 1036px;
    color: var(--ink-soft);
  }
  .recipient__label {
    font-size: 23px;
    font-weight: 400;
    line-height: 36px;
  }
  .recipient__field {
    font-size: 23px;
    font-weight: 500;
    line-height: 37px;
    padding-left: 3px;
  }
  .recipient__field--name { margin-top: 16px; }
</style>
</head>
<body>
  <main class="cover">
    <div class="accent-band accent-band--top"></div>
    <div class="accent-band accent-band--bottom"></div>

    <div class="hero-photo" role="img" aria-label="Photograph looking up at tall city skyscrapers against a cloudy sky"></div>

    <header class="brand">Northfield Advisory</header>

    <h1 class="title">Growth Leader</h1>
    <div class="title-tag">Assessment</div>

    <section class="recipient">
      <p class="recipient__label">Insight Report for</p>
      <p class="recipient__field recipient__field--name">Name</p>
      <p class="recipient__field">Date</p>
    </section>
  </main>
</body>
</html>
```